Promotional business a5 Notepad design

I am looking for a custom a5 notepad design as a promotional item to give away to customers etc.
Attached will be a desk planner we had designed feel free to use as a reference.
We want the notepad to have lines running horizontal not squares like the desk planner example.

Industry/Entity Type

Hydraulic / industrial

Colors

Designer to choose colors to be used in the design.

```html
<!DOCTYPE html>
<html lang="en">
<head>
<meta charset="utf-8">
<title>Unified Hose and Couplings – A5 Notepad</title>
<link href="https://fonts.googleapis.com/css2?family=Arimo:wght@400;700&display=swap" rel="stylesheet">
<style>
  :root {
    --backdrop: #a2a2a4;
    --paper: #ffffff;
    --brand-blue: #142dbd;
    --ink-dark: #1b1b1b;
    --rule: #7a7a7a;
    --steel-start: #8c8c8c;
    --steel-end: #e2e2e2;
    --footer-text: #ffffff;
  }
  html, body {
    margin: 0;
    padding: 0;
    width: 1200px;
    height: 900px;
    overflow: hidden;
    background: var(--backdrop);
    font-family: "Arimo", Arial, sans-serif;
  }
  .notepad {
    position: absolute;
    left: 325px;
    top: 60px;
    width: 550px;
    height: 780px;
    background: var(--paper);
    overflow: hidden;
  }
  .brand {
    position: absolute;
    left: 40px;
    top: 25px;
    width: 206px;
    height: 46px;
    display: flex;
    align-items: center;
    gap: 8px;
  }
  .brand-dot {
    flex: none;
    width: 44px;
    height: 44px;
    border-radius: 50%;
    background: var(--ink-dark);
  }
  .brand-name {
    font-weight: 700;
    font-size: 14px;
    line-height: 17px;
    letter-spacing: 0.4px;
    color: var(--ink-dark);
    text-transform: uppercase;
  }
  .brand-name span { display: block; white-space: nowrap; }
  .header-bar {
    position: absolute;
    left: 254px;
    right: 0;
    top: 33px;
    height: 18px;
    background: var(--brand-blue);
  }
  .header-steel {
    position: absolute;
    left: 254px;
    right: 0;
    top: 54px;
    height: 8px;
    background: linear-gradient(to right, var(--steel-start), var(--steel-end));
  }
  .ruling {
    position: absolute;
    left: 37px;
    width: 475px;
    top: 123px;
    height: 562px;
    background: repeating-linear-gradient(
      to bottom,
      var(--rule) 0,
      var(--rule) 1px,
      transparent 1px,
      transparent 29.47px
    );
  }
  .footer {
    position: absolute;
    left: 0;
    right: 0;
    bottom: 0;
    height: 56px;
    background: var(--brand-blue);
    color: var(--footer-text);
    text-align: center;
  }
  .service-area {
    margin-top: 11px;
    font-size: 11px;
    line-height: 13px;
  }
  .contact-line {
    margin-top: 4px;
    font-size: 12.5px;
    line-height: 15px;
  }
  .contact-item { margin: 0 3px; white-space: nowrap; }
  .icon {
    display: inline-block;
    vertical-align: -1px;
    margin-right: 3px;
    fill: var(--footer-text);
  }
</style>
</head>
<body>
  <main class="notepad">
    <header>
      <div class="brand">
        <span class="brand-dot"></span>
        <span class="brand-name"><span>Unified Hose</span><span>and Couplings</span></span>
      </div>
      <div class="header-bar"></div>
      <div class="header-steel"></div>
    </header>

    <section class="ruling" aria-label="Ruled writing lines"></section>

    <footer class="footer">
      <div class="service-area">
        <svg class="icon" width="8" height="10" viewBox="0 0 8 10" aria-hidden="true"><path d="M4 0a4 4 0 0 0-4 4c0 3 4 6 4 6s4-3 4-6a4 4 0 0 0-4-4zm0 5.6A1.6 1.6 0 1 1 4 2.4a1.6 1.6 0 0 1 0 3.2z"/></svg>Servicing The Adelaide Metropolitan Area
      </div>
      <div class="contact-line">
        <span class="contact-item"><svg class="icon" width="9" height="9" viewBox="0 0 10 10" aria-hidden="true"><path d="M2 0.5l1.8 2.2-1 1.1c.6 1.3 1.6 2.3 2.9 2.9l1.1-1 2.2 1.8-1 1.9C5 9.3.7 5 .1 1.5z"/></svg>08 8100 4520</span>
        <span class="contact-item"><svg class="icon" width="9" height="9" viewBox="0 0 10 10" aria-hidden="true"><path d="M2 0.5l1.8 2.2-1 1.1c.6 1.3 1.6 2.3 2.9 2.9l1.1-1 2.2 1.8-1 1.9C5 9.3.7 5 .1 1.5z"/></svg>0400 123 456</span>
        <span class="contact-item"><svg class="icon" width="10" height="7" viewBox="0 0 10 7" aria-hidden="true"><path d="M0 0h10v7H0zM.8.8v.4L5 4l4.2-2.8V.8L5 3.4z"/></svg>email@unifiedhose.com.au</span>
      </div>
    </footer>
  </main>
</body>
</html>
```